Kelvaro.ch is looking for business card letterhead and envelope C5 with WOW effect

We need a strong business card for our company Kelvaro.ch, logo is available. You want a black or dark background on which the logo Stark r% 26 # 252; appears. Letterhead and envelope in C5 format should be in a similar design, but does not have to be We need a strong business card for our company Kelvaro.ch, logo is available. A black or dark background is desired, on which the logo Stark comes across. The letterhead and the envelope in C5 format should have a similar design.

Target Market(s)

Private customers as well as entrepreneurs

Contact Information for Business Card

E-mail: info@kelvaro-example.ch
Web.www.Kelvaro-example.ch
Tel: +41 ( 0 ) 79 482 6037
Adresse:
Lindenweg 14
9406 Tarnbach

Hier kann man Icons verwenden für Email,Tel und Adressse

Font styles to use
Other font styles liked:
• Dubai,bold

Colors

Designer to choose colors to be used in the design.

Requirements
Must have
• WOW effect
Nice to have
• R% 26 # 252; back business card with our service listings. - VEHICLE LABELING - SHOP WINDOW LABELING - STICKERS AND MUCH MORE ... in red color

```html
<!DOCTYPE html>
<html lang="en">
<head>
<meta charset="utf-8">
<title>Kelvaro.ch – Business Card</title>
<link rel="stylesheet" href="https://fonts.googleapis.com/css2?family=Ubuntu:wght@400;500;700&family=Open+Sans:wght@400&display=swap">
<style>
  :root {
    --stage: #1c1c1c;
    --card: #262626;
    --card-edge: #2e2e2e;
    --yellow: #fcc91c;
    --white: #f4f4f4;
    --red: #d6202a;
  }
  html, body {
    margin: 0;
    width: 1200px;
    height: 900px;
    overflow: hidden;
    background: var(--stage);
  }
  .stage {
    position: relative;
    width: 1200px;
    height: 900px;
  }
  .card {
    position: absolute;
    left: 260px;
    width: 680px;
    height: 388px;
    background: linear-gradient(135deg, var(--card) 0%, var(--card-edge) 60%, var(--card) 100%);
    box-shadow: 0 14px 30px rgba(0,0,0,.55);
    overflow: hidden;
  }
  .card--front { top: 42px; }
  .card--back { top: 470px; }

  /* front */
  .brand {
    position: absolute;
    left: 200px;
    top: 128px;
    display: flex;
    align-items: center;
    gap: 16px;
  }
  .brand__mark {
    width: 30px;
    height: 30px;
    background: var(--yellow);
    border-radius: 50%;
  }
  .brand__name {
    font-family: "Ubuntu", sans-serif;
    font-weight: 700;
    font-size: 48px;
    letter-spacing: 1px;
    color: var(--white);
  }
  .services {
    position: absolute;
    right: 150px;
    top: 232px;
    margin: 0;
    padding: 0;
    list-style: none;
    text-align: right;
    font-family: "Open Sans", sans-serif;
    font-size: 16px;
    line-height: 22px;
    color: var(--white);
  }
  .services li::after {
    content: "";
    display: inline-block;
    width: 7px;
    height: 7px;
    margin-left: 14px;
    border: 2px solid var(--red);
    border-radius: 50%;
    vertical-align: middle;
  }

  /* back */
  .pattern-area {
    position: absolute;
    left: 0;
    top: 0;
    width: 300px;
    height: 388px;
  }
  .person {
    position: absolute;
    right: 44px;
    top: 48px;
    text-align: right;
    font-family: "Ubuntu", sans-serif;
  }
  .person__name {
    margin: 0;
    font-weight: 700;
    font-size: 26px;
    letter-spacing: 3px;
    color: var(--white);
  }
  .person__name span { color: var(--yellow); }
  .person__role {
    margin: 4px 0 0;
    font-size: 16px;
    letter-spacing: 1px;
    color: var(--white);
  }
  .accent-bar {
    position: absolute;
    right: 0;
    top: 60px;
    width: 16px;
    height: 50px;
    background: var(--yellow);
  }
  .contact {
    position: absolute;
    right: 36px;
    top: 236px;
    margin: 0;
    padding: 0;
    list-style: none;
    font-family: "Ubuntu", sans-serif;
    font-size: 18px;
    color: var(--white);
    text-align: right;
  }
  .contact li {
    display: flex;
    justify-content: flex-end;
    align-items: center;
    gap: 12px;
    height: 27px;
  }
  .contact svg { width: 16px; height: 16px; }
  .divider {
    position: absolute;
    right: 36px;
    top: 330px;
    width: 44px;
    height: 1px;
    background: var(--yellow);
  }
  .address {
    position: absolute;
    right: 36px;
    top: 342px;
    margin: 0;
    font-family: "Ubuntu", sans-serif;
    font-size: 18px;
    letter-spacing: .5px;
    color: var(--white);
  }
</style>
</head>
<body>
<main class="stage">

  <section class="card card--front">
    <div class="brand">
      <span class="brand__mark"></span>
      <span class="brand__name">KELVARO.CH</span>
    </div>
    <ul class="services">
      <li>VEHICLE LABELING</li>
      <li>SHOP WINDOW LABELING</li>
      <li>STICKERS AND MUCH MORE</li>
    </ul>
  </section>

  <section class="card card--back">
    <svg class="pattern-area" viewBox="0 0 300 388" role="img" aria-label="Yellow honeycomb pattern decoration">
      <defs>
        <linearGradient id="honeyFade" x1="0" y1="1" x2="1" y2="0">
          <stop offset="0" stop-color="#fcc91c"/>
          <stop offset="0.55" stop-color="#c99f14"/>
          <stop offset="1" stop-color="#262626"/>
        </linearGradient>
      </defs>
      <rect width="300" height="388" fill="url(#honeyFade)"/>
    </svg>

    <div class="person">
      <p class="person__name">LUKAS <span>BRENNER</span></p>
      <p class="person__role">Director</p>
    </div>
    <div class="accent-bar"></div>

    <ul class="contact">
      <li>+41 ( 0 ) 79 482 6037
        <svg viewBox="0 0 16 16" aria-hidden="true"><path d="M4 1.5l2.2 3-1.4 1.6c.8 1.9 2.2 3.4 4.1 4.3l1.6-1.4 3 2.2-1.3 2.6C7 13.5 2.5 9 1.5 2.8z" fill="none" stroke="var(--yellow)" stroke-width="1.4" stroke-linejoin="round"/></svg>
      </li>
      <li>info@kelvaro-example.ch
        <svg viewBox="0 0 16 16" aria-hidden="true"><rect x="1.5" y="3.5" width="13" height="9" fill="none" stroke="var(--yellow)" stroke-width="1.4"/><polyline points="1.5,3.5 8,9 14.5,3.5" fill="none" stroke="var(--yellow)" stroke-width="1.4"/></svg>
      </li>
      <li>www.kelvaro-example.ch
        <svg viewBox="0 0 16 16" aria-hidden="true"><g fill="none" stroke="var(--yellow)" stroke-width="1.2"><circle cx="8" cy="8" r="6.5"/><ellipse cx="8" cy="8" rx="3" ry="6.5"/><line x1="1.5" y1="8" x2="14.5" y2="8"/><line x1="2.5" y1="4.5" x2="13.5" y2="4.5"/><line x1="2.5" y1="11.5" x2="13.5" y2="11.5"/></g></svg>
      </li>
    </ul>
    <div class="divider"></div>
    <p class="address">Lindenweg 14 9406 Tarnbach</p>
  </section>

</main>
</body>
</html>
```